Professional & attention grabbing.

A business card design, front and back. I already have a logo I will attach, but I am open to something new as well.
Things to include:
Name:
Title:
Phone:
Email:
Wanting something that is professional but attention grabbing.
Also we do a lot of work using drones on natural gas pipelines (leading the future)if you want to include any of that. I'm open to ideas.
Target Market(s)
Natural gas transmission industry / greenhouse gas mitigation industry
Industry/Entity Type
Business
Colors
Designer to choose colors to be used in the design.
Look and feel
Each slider illustrates characteristics of the customer's brand and the style your logo design should communicate.

```html
<!DOCTYPE html>
<html lang="en">
<head>
<meta charset="utf-8">
<title>Kestrel Line Inspections — Business Card</title>
<link href="https://fonts.googleapis.com/css2?family=Roboto+Condensed:wght@400;700&display=swap" rel="stylesheet">
<style>
  :root {
    --stage: #232323;
    --card-white: #ffffff;
    --brand-red: #c8161d;
    --brand-red-dark: #a50f15;
    --ink: #3a3a3a;
    --ink-soft: #6b6b6b;
    --paper-on-red: #ffffff;
  }
  * { box-sizing: border-box; margin: 0; padding: 0; }
  html, body {
    width: 1200px; height: 950px; overflow: hidden;
    background: var(--stage);
    font-family: "Roboto Condensed", Arial, sans-serif;
  }
  .canvas { position: relative; width: 1200px; height: 950px; }

  .card {
    position: absolute; left: 250px; width: 700px; height: 400px;
    overflow: hidden;
  }
  .card--front { top: 50px; background: var(--card-white); }
  .card--back {
    top: 500px;
    background: linear-gradient(135deg, var(--brand-red-dark), var(--brand-red) 55%, #d4343a);
  }

  /* shared brand lockup */
  .brand {
    position: absolute; display: flex; align-items: center; gap: 14px;
    font-weight: 700; letter-spacing: 0.5px; white-space: nowrap;
  }
  .brand__square { width: 30px; height: 30px; background: var(--brand-red); flex: none; }

  /* front */
  .corner-tab {
    position: absolute; top: 0; right: 0;
    width: 110px; height: 18px; background: var(--brand-red);
  }
  .card--front .brand { top: 110px; right: 48px; color: var(--ink); font-size: 32px; }

  .contact-block { position: absolute; left: 48px; bottom: 48px; }
  .person__name {
    color: var(--brand-red); font-size: 26px; font-weight: 400;
    letter-spacing: 1px; text-transform: uppercase;
  }
  .person__title {
    color: var(--ink); font-size: 18px; text-transform: uppercase;
    letter-spacing: 1px; margin-bottom: 16px;
  }
  .contact-list { list-style: none; }
  .contact-list li {
    display: flex; align-items: center; gap: 12px;
    color: var(--ink-soft); font-size: 17px; margin-top: 7px;
  }
  .contact-icon {
    width: 20px; height: 20px; border-radius: 50%;
    background: var(--brand-red); display: flex; align-items: center; justify-content: center;
  }

  /* back */
  .card--back .brand {
    top: 50%; left: 50%; transform: translate(-50%, -50%);
    color: var(--paper-on-red); font-size: 40px;
  }
  .card--back .brand__square { width: 36px; height: 36px; background: var(--paper-on-red); }
  .back-web {
    position: absolute; left: 26px; top: 50%;
    transform: translateY(-50%);
    writing-mode: vertical-rl;
    color: var(--paper-on-red); font-size: 14px; letter-spacing: 6px;
    white-space: nowrap; opacity: 0.9;
  }
</style>
</head>
<body>
<main class="canvas">

  <section class="card card--front" aria-label="Card front">
    <div class="corner-tab"></div>
    <div class="brand">
      <span class="brand__square"></span>
      <span class="brand__name">Kestrel Line Inspections</span>
    </div>

    <div class="contact-block">
      <p class="person__name">Mara Ellison</p>
      <p class="person__title">President</p>
      <ul class="contact-list">
        <li>
          <span class="contact-icon">
            <svg width="11" height="11" viewBox="0 0 24 24"><path fill="#fff" d="M6.6 10.8a15 15 0 0 0 6.6 6.6l2.2-2.2a1 1 0 0 1 1-.25 11.4 11.4 0 0 0 3.6.6 1 1 0 0 1 1 1V20a1 1 0 0 1-1 1A17 17 0 0 1 3 4a1 1 0 0 1 1-1h3.5a1 1 0 0 1 1 1c0 1.25.2 2.45.6 3.6a1 1 0 0 1-.25 1z"/></svg>
          </span>555 014 7788
        </li>
        <li>
          <span class="contact-icon">
            <svg width="11" height="11" viewBox="0 0 24 24"><path fill="#fff" d="M2 5h20v14H2z"/><path fill="none" stroke="#c8161d" stroke-width="2" d="M2 5l10 8 10-8"/></svg>
          </span>mara@kestrelline.com
        </li>
        <li>
          <span class="contact-icon">
            <svg width="11" height="11" viewBox="0 0 24 24"><circle cx="12" cy="12" r="9" fill="none" stroke="#fff" stroke-width="2.5"/><path stroke="#fff" stroke-width="2" d="M3 12h18M12 3c-4 5-4 13 0 18M12 3c4 5 4 13 0 18" fill="none"/></svg>
          </span>www.kestrelline.com
        </li>
      </ul>
    </div>
  </section>

  <section class="card card--back" aria-label="Card back">
    <p class="back-web">www.kestrelline.com</p>
    <div class="brand">
      <span class="brand__square"></span>
      <span class="brand__name">Kestrel Line Inspections</span>
    </div>
  </section>

</main>
</body>
</html>
```